Business Card Design (NEW FILES)

ATTENTION: New vector files are available. Please update your design to reflect/use the new (better resolution) logo images.

Seeking a unique and professional business card design for a commercial drone photography/videography business. The layout should feature
the logo (attached) and include the following information:
Owen Tarrick
614-502-7738
www.skylarkreelworks.example
NRD Certified Remote Pilot

Owen Tarrick

```html
<!DOCTYPE html>
<html lang="en">
<head>
<meta charset="utf-8">
<title>Skylark Reelworks – Business Card</title>
<link href="https://fonts.googleapis.com/css2?family=Lato:wght@400;700;900&display=swap" rel="stylesheet">
<style>
  :root{
    --backdrop:#8f8f8f;
    --paper:#ffffff;
    --navy:#131a46;
    --orange:#ec8a4a;
    --ink:#1b2150;
    --bar-1:#5b2d91;
    --bar-2:#c2168c;
    --bar-3:#e4221f;
    --bar-4:#f08a24;
    --bar-5:#9ccb2c;
    --bar-6:#1bb3b3;
  }
  *{box-sizing:border-box;margin:0;padding:0}
  html,body{width:1200px;height:1200px;overflow:hidden;background:var(--backdrop)}
  body{position:relative;font-family:"Lato",sans-serif}
  .card{position:absolute;left:281px;width:641px;height:366px;border-radius:16px;overflow:hidden}
  .card--front{top:195px;background:var(--paper)}
  .card--back{top:639px;background:var(--navy)}

  .brand{position:absolute;display:flex;align-items:center;gap:10px;font-weight:700;white-space:nowrap}
  .brand__dot{border-radius:50%;background:var(--orange);flex:none}
  .card--front .brand{right:43px;top:92px;font-size:27px;color:var(--navy)}
  .card--front .brand__dot{width:16px;height:16px}
  .card--back .brand{left:50%;top:50%;transform:translate(-50%,-50%);font-size:44px;color:#fff}
  .card--back .brand__dot{width:24px;height:24px}

  .holder{position:absolute;left:43px;top:175px}
  .holder__name{font-weight:900;font-size:27px;color:var(--ink);line-height:1;letter-spacing:.2px}
  .holder__role{font-size:17px;color:var(--orange);margin-top:6px;line-height:1}

  .spectrum{position:absolute;left:44px;top:245px;width:554px;display:flex;gap:3px}
  .spectrum span{flex:1;height:3px}

  .contacts{position:absolute;left:42px;top:264px;list-style:none;font-size:16px;color:var(--ink)}
  .contacts li{display:flex;align-items:center;gap:9px;height:22.5px}
  .contacts svg{width:12px;height:12px;flex:none}

  .credentials{position:absolute;right:43px;top:286px;text-align:right;line-height:22.5px}
  .credentials__cert{font-size:16px;color:var(--ink)}
  .credentials__insured{font-size:17px;font-weight:900;color:var(--orange);letter-spacing:.5px}
</style>
</head>
<body>
  <section class="card card--front">
    <div class="brand"><span class="brand__name">Skylark Reelworks</span><span class="brand__dot"></span></div>

    <div class="holder">
      <p class="holder__name">OWEN TARRICK</p>
      <p class="holder__role">Owner</p>
    </div>

    <div class="spectrum">
      <span style="background:var(--bar-1)"></span>
      <span style="background:var(--bar-2)"></span>
      <span style="background:var(--bar-3)"></span>
      <span style="background:var(--bar-4)"></span>
      <span style="background:var(--bar-5)"></span>
      <span style="background:var(--bar-6)"></span>
    </div>

    <ul class="contacts">
      <li>
        <svg viewBox="0 0 12 12" aria-hidden="true"><path fill="#ec8a4a" d="M2.4 0.8l1.8 0 0.8 2.4-1.2 0.9c0.6 1.4 1.6 2.4 3 3l0.9-1.2 2.4 0.8 0 1.8c0 0.6-0.5 1.1-1.1 1.1C4.7 9.6 1.3 6.2 1.3 1.9c0-0.6 0.5-1.1 1.1-1.1z"/></svg>
        <span>614-502-7738</span>
      </li>
      <li>
        <svg viewBox="0 0 12 12" aria-hidden="true"><rect x="0.5" y="2" width="11" height="8" rx="1" fill="#ec8a4a"/><path d="M1 2.6l5 3.6 5-3.6" fill="none" stroke="#fff" stroke-width="1"/></svg>
        <span>owen@skylarkreelworks.example</span>
      </li>
      <li>
        <svg viewBox="0 0 12 12" aria-hidden="true"><circle cx="6" cy="6" r="5.5" fill="#ec8a4a"/><path d="M0.5 6h11M6 0.5c-2 2.5-2 8.5 0 11M6 0.5c2 2.5 2 8.5 0 11" fill="none" stroke="#fff" stroke-width="0.8"/></svg>
        <span>www.skylarkreelworks.example</span>
      </li>
    </ul>

    <div class="credentials">
      <p class="credentials__cert">NRD Certified Remote Pilot</p>
      <p class="credentials__insured">FULLY INSURED</p>
    </div>
  </section>

  <section class="card card--back">
    <div class="brand"><span class="brand__name">Skylark Reelworks</span><span class="brand__dot"></span></div>
  </section>
</body>
</html>
```